Marla’s Sandwich Corner Grand Opening Door Flyer

1. Project Title
• “Flyer Design for Sandwich Shop Grand Opening”
• Why it’s effective: Direct and to the point, highlighting the purpose of the design.

2. Project Description
• “We’re looking for a professional designer to create a vibrant and modern flyer for our sandwich shop, Marla’s Corner. The flyer should emphasize our handcrafted sandwiches, fresh-baked bread, and house-made meats. As a women & family-owned business, we want this aspect prominently displayed. The flyer should also include our logo, a ‘Grand Opening’ and our website: MarlasCorner.example. We want the design to be clean, bold, and visually appealing to attract customers. We also would like a QR code so they can scan to load of the website to order online, but also list it.
• Why it’s effective: Clear goals, modern style preference, and necessary details outlined.

3. Visual Style
• “Modern, bold, and clean design with bright, appetizing colors. Focus on high-quality imagery of sandwiches, sleek fonts, and an inviting layout.”
• Why it’s effective: Communicates the desired aesthetic and tone.

4. Key Details to Include
• Business Name: Marla’s Sandwich Corner
• Taglines:
“Women & Family Owned”
“Handcrafted Sandwiches Made with Love”
“Fresh Baked Bread”
“House-made Slow Roasted House Specialties”
“Gluten-Friendly”
“Vegan-Friendly”
“7:00am Fresh Daily Grounded Coffee and Breakfast”

• Call-to-Action: “Order Online at MarlasCorner.example”
• Placeholder for the logo.
• Size: 4.25 x 11 (Door Hanger)
• File Format: High-resolution PDF, JPEG, or PNG.
• Print-Ready: Include bleed margins and ensure print clarity.

6. Tone
• Friendly and professional. Highlighting that your business is women-owned adds a unique and personal touch vs deli meat shops. We are a gourmet sandwich shop, with fresh baked bread, house-made meats, with gluten and vegan options. Each sandwich is made with love.

Target Market(s)

Coffee drinkers for morning crowd and sandwiches for lunch

Industry/Entity Type

Sandwich Shop

Colors
EB3D1F
EC4F4E
F09395
F8D3D4
FCEDEE

Requirements
Must have
• See Description
Nice to have
• Use website to get a feel for color theme
Should not have
• NA

```html
<!DOCTYPE html>
<html lang="en">
<head>
<meta charset="utf-8">
<title>Marla’s Sandwich Corner — Grand Opening Door Hanger</title>
<link rel="stylesheet" href="https://fonts.googleapis.com/css2?family=Anton&family=Montserrat:wght@700;800&family=Arimo:wght@700&display=swap">
<style>
  :root {
    --orange: #eb3d1f;
    --pink: #f5c1d9;
    --pink-soft: #fcedee;
    --paper: #ffffff;
    --ink: #111111;
    --panel: #0d0d0d;
    --gold: #e9c22a;
    --brown: #4a1d0c;
    --cream: #fde3bd;
    --sun: #fff000;
    --stage: #e4e2de;
    --photo-light: #e8b46c;
    --photo-dark: #b97a40;
  }
  * { box-sizing: border-box; margin: 0; padding: 0; }
  html, body { width: 1200px; height: 1200px; overflow: hidden; }
  body {
    background: var(--stage);
    position: relative;
    font-family: "Montserrat", Arial, sans-serif;
  }
  .hanger {
    position: absolute;
    top: 175px;
    width: 340px;
    height: 850px;
    background: var(--paper);
    overflow: hidden;
    box-shadow: 0 12px 26px rgba(0,0,0,0.18);
  }
  .hanger--back { left: 190px; }
  .hanger--front { left: 670px; }

  .top-band { position: absolute; left: 0; top: 0; width: 100%; height: 18px; background: var(--pink); }
  .top-rule { position: absolute; top: 18px; height: 3px; width: 62px; background: var(--orange); }
  .top-rule--left { left: 0; }
  .top-rule--right { right: 0; }

  .hook-tab {
    position: absolute; left: 62px; top: 0; width: 216px; height: 300px;
    background: var(--pink); border-radius: 0 0 108px 108px;
  }
  .hook-hole {
    position: absolute; left: 83px; top: 48px; width: 174px; height: 174px;
    border-radius: 50%; background: var(--paper);
    border: 2px dashed #6d6d6d; outline: 6px solid var(--paper);
  }
  .hook-hole--emblem { background: var(--sun); }

  .body-column {
    position: absolute; left: 24px; right: 24px; top: 270px; bottom: 0;
    background: var(--pink);
  }
  .cut-line {
    position: absolute; top: 390px; height: 330px; width: 0;
    border-left: 1.5px dashed #333;
  }
  .cut-line--left { left: 32px; }
  .cut-line--right { right: 32px; }

  .brand-name {
    position: absolute; left: 0; right: 0; top: 296px;
    text-align: center; color: var(--orange);
    font-family: "Montserrat", Arial, sans-serif; font-weight: 800;
    font-size: 31px; line-height: 1.05; letter-spacing: -0.5px;
  }

  .info-panel {
    position: absolute; left: 40px; right: 40px; top: 378px; height: 290px;
    background: var(--panel); border-radius: 30px 30px 6px 6px;
    text-align: center; color: #fff;
  }
  .taglines {
    list-style: none; padding-top: 18px;
    font-family: "Arimo", Arial, sans-serif; font-weight: 700;
    font-size: 9.8px; line-height: 17px; white-space: nowrap;
  }
  .headline {
    font-family: "Anton", Impact, sans-serif; color: var(--gold);
    text-transform: uppercase; line-height: 0.95;
    text-shadow: 0 3px 0 var(--brown), 0 5px 0 var(--brown);
  }
  .headline__top { display: block; font-size: 58px; margin-top: 10px; }
  .headline__bottom { display: block; font-size: 76px; letter-spacing: 1px; }

  .ribbon {
    position: absolute; left: 70px; right: 70px; top: 662px; height: 26px;
    background: var(--brown); border-radius: 4px;
    color: var(--gold); font-family: "Montserrat", Arial, sans-serif; font-weight: 700;
    font-size: 12px; letter-spacing: 5px; text-align: center; line-height: 26px;
  }

  .cream-dome {
    position: absolute; left: -40px; right: -40px; top: 730px; height: 260px;
    background: var(--cream); border-radius: 50% 50% 0 0;
  }
  .food-photo {
    position: absolute; left: 80px; top: 698px; width: 180px; height: 92px;
    border-radius: 6px;
    background: linear-gradient(160deg, var(--photo-light), var(--photo-dark));
  }
  .cta {
    position: absolute; left: 0; right: 0; top: 796px;
    text-align: center; color: var(--ink);
    font-family: "Montserrat", Arial, sans-serif; font-weight: 700;
    font-size: 15.5px; line-height: 1.12; text-transform: uppercase;
  }
  .cta__url { display: block; font-size: 16px; }
  .base-bar {
    position: absolute; left: 70px; right: 70px; bottom: -8px; height: 16px;
    background: var(--ink); border-radius: 10px;
  }
</style>
</head>
<body>

  <article class="hanger hanger--back">
    <div class="top-band"></div>
    <div class="top-rule top-rule--left"></div>
    <div class="top-rule top-rule--right"></div>
    <div class="body-column"></div>
    <div class="hook-tab"></div>
    <div class="hook-hole"></div>
    <div class="cut-line cut-line--left"></div>
    <div class="cut-line cut-line--right"></div>
    <h1 class="brand-name">Marla’s<br>Sandwich Corner</h1>
    <section class="info-panel">
      <ul class="taglines">
        <li>Women &amp; Family Owned</li>
        <li>Handcrafted Sandwiches Made with Love</li>
        <li>Fresh Baked Bread</li>
        <li>House-made Slow Roasted House Specialties</li>
        <li>Gluten-Friendly</li>
        <li>Vegan-Friendly</li>
        <li>7:00am Fresh Daily Grounded Coffee and Breakfast</li>
      </ul>
      <h2 class="headline"><span class="headline__top">Grand</span><span class="headline__bottom">Opening</span></h2>
    </section>
    <div class="ribbon">...CEREMONY...</div>
    <div class="cream-dome"></div>
    <div class="food-photo" role="img" aria-label="Photo of a crispy chicken sandwich on a wooden board"></div>
    <p class="cta">Order online at<span class="cta__url">www.marlascorner.example</span></p>
    <div class="base-bar"></div>
  </article>

  <article class="hanger hanger--front">
    <div class="top-band"></div>
    <div class="top-rule top-rule--left"></div>
    <div class="top-rule top-rule--right"></div>
    <div class="body-column"></div>
    <div class="hook-tab"></div>
    <div class="hook-hole hook-hole--emblem" role="img" aria-label="Round yellow brand emblem"></div>
    <div class="cut-line cut-line--left"></div>
    <div class="cut-line cut-line--right"></div>
    <h1 class="brand-name">Marla’s<br>Sandwich Corner</h1>
    <section class="info-panel">
      <ul class="taglines">
        <li>Women &amp; Family Owned</li>
        <li>Handcrafted Sandwiches Made with Love</li>
        <li>Fresh Baked Bread</li>
        <li>House-made Slow Roasted House Specialties</li>
        <li>Gluten-Friendly</li>
        <li>Vegan-Friendly</li>
        <li>7:00am Fresh Daily Grounded Coffee and Breakfast</li>
      </ul>
      <h2 class="headline"><span class="headline__top">Grand</span><span class="headline__bottom">Opening</span></h2>
    </section>
    <div class="ribbon">...CEREMONY...</div>
    <div class="cream-dome"></div>
    <div class="food-photo" role="img" aria-label="Photo of a crispy chicken sandwich on a wooden board"></div>
    <p class="cta">Order online at<span class="cta__url">www.marlascorner.example</span></p>
    <div class="base-bar"></div>
  </article>

</body>
</html>
```